Wedding Invitation to be used digitally

Design of a Wedding Invitation.
It will be used digitally by whatsapp, so the file format and image size should be appropriate. We don´t intend to print.
Word file with the text contents as attachment. This is REALLY just the text and the main sequencial order of the information that should appear in the invitation.
However, ALL criativity is welcome ofcourse in terms of organization of the information in the paper, font, uppercase and lowercase, numbers and their format, dates and their format, drawings, logo, etc etc

Target Market(s)

family and friends

Requirements
Must have
• A logo at the top with the capitals of our name - R and T
Nice to have
• Should be elegant

```html
<!DOCTYPE html>
<html lang="en">
<head>
<meta charset="utf-8">
<title>Rita &amp; Tomás — Wedding Invitation</title>
<link rel="stylesheet" href="https://fonts.googleapis.com/css2?family=Playfair+Display:wght@400&display=swap">
<style>
  :root {
    --backdrop: #efeceb;
    --card: #ccb79e;
    --ampersand: #ab9175;
    --ink: #1f1d1b;
    --light: #ffffff;
    --frame: #e9dfd2;
    --monogram: #3a3634;
  }
  html, body {
    margin: 0;
    width: 1200px;
    height: 854px;
    overflow: hidden;
    background: var(--backdrop);
  }
  .canvas {
    position: relative;
    width: 1200px;
    height: 854px;
    font-family: "Playfair Display", Georgia, serif;
  }
  .invitation {
    position: absolute;
    left: 360px;
    top: 106px;
    width: 451px;
    height: 637px;
    background: var(--card);
  }
  .frame {
    position: absolute;
    left: 32px;
    top: 106px;
    width: 388px;
    height: 467px;
    border: 1px solid var(--frame);
    box-sizing: border-box;
  }
  .frame-gap {
    position: absolute;
    left: 150px;
    top: 104px;
    width: 164px;
    height: 4px;
    background: var(--card);
  }
  .monogram {
    position: absolute;
    left: 111px;
    top: 25px;
    width: 230px;
    height: 180px;
  }
  .line {
    position: absolute;
    left: 0;
    width: 100%;
    margin: 0;
    text-align: center;
    line-height: 1;
    white-space: nowrap;
    font-weight: 400;
  }
  .kicker {
    font-size: 11.5px;
    letter-spacing: 2.2px;
    color: var(--ink);
  }
  .ampersand {
    font-size: 92px;
    color: var(--ampersand);
  }
  .name {
    font-size: 36px;
    color: var(--light);
  }
  .divider {
    position: absolute;
    left: 196px;
    top: 392px;
    width: 60px;
    height: 1px;
    background: var(--light);
  }
  .date {
    font-size: 15px;
    color: var(--ink);
  }
  .detail {
    font-size: 11px;
    color: var(--ink);
  }
  .rsvp {
    position: absolute;
    left: 26px;
    top: 597px;
    margin: 0;
    font-size: 11px;
    letter-spacing: 1.6px;
    color: var(--light);
    line-height: 1;
  }
</style>
</head>
<body>
<div class="canvas">
  <article class="invitation">
    <div class="frame"></div>
    <div class="frame-gap"></div>

    <svg class="monogram" viewBox="0 0 230 180" role="img" aria-label="Calligraphic R and T monogram">
      <ellipse cx="115" cy="90" rx="110" ry="82" fill="#b9a58d" opacity="0.45"/>
    </svg>

    <p class="line kicker" style="top:219px">TOGETHER WITH THEIR FAMILIES</p>
    <p class="line ampersand" style="top:245px">&amp;</p>
    <h1 class="line name" style="top:240px">RITA LENZ</h1>
    <h1 class="line name" style="top:310px">TOMÁS VARELA</h1>
    <p class="line kicker" style="top:361px; letter-spacing:1.8px">INVITE YOU TO THEIR WEDDING CELEBRATION</p>

    <div class="divider"></div>

    <p class="line date" style="top:410px">SUNDAY, JULY 28, 2024</p>
    <p class="line date" style="top:427px">AT 11h30</p>

    <p class="line detail" style="top:456px">CAPELA DE SANTA LUZIA | CASCAIS</p>
    <p class="line detail" style="top:469px">(PARKING – MARINA DO FAROL OR PARQUE TERRA AZUL)</p>
    <p class="line detail" style="top:494px">RECEPTION TO FOLLOW</p>
    <p class="line detail" style="top:520px">AT</p>
    <p class="line detail" style="top:532px">HOTEL FORTE DA MARÉ RESIDENCES | CASCAIS</p>
    <p class="line detail" style="top:545px">(PARKING – ON SITE)</p>

    <p class="rsvp">RSVP BY 20TH JULY</p>
  </article>
</div>
</body>
</html>
```